Modern Business Card

Modern professional business card with more than just logo and demographic info. Something memorable.

We are a trendy/modern chiropractic group with an emphasis on neurology, hence the minimalist-type brain logo. We want to convey that modern and technical aspect with professionalism and the elite nature of our practice environment.

```html
<!DOCTYPE html>
<html lang="en">
<head>
<meta charset="utf-8">
<title>Meridian Chiropractic – Business Card</title>
<link rel="stylesheet" href="https://fonts.googleapis.com/css2?family=Lato:wght@400;700&display=swap">
<style>
  :root{
    --brand-blue:#4a80c8;
    --rule-grey:#5c5c5c;
    --ink:#2b2b2b;
    --ink-soft:#4a4a4a;
    --card-white:#ffffff;
    --backdrop:#e9ecf1;
  }
  *{box-sizing:border-box;margin:0;padding:0}
  html,body{width:1049px;height:1200px;overflow:hidden}
  body{background:var(--backdrop);font-family:'Lato',sans-serif;color:var(--ink);position:relative}

  .card{position:absolute;left:176px;width:698px;height:398px;background:var(--card-white);
        border:1.5px solid var(--brand-blue);box-shadow:0 3px 6px rgba(0,0,0,.25);overflow:hidden}
  .card--front{top:159px;border-radius:26px 0 26px 0}
  .card--back{top:643px;border-radius:0 26px 0 26px}

  .dot-field{position:absolute}
  .card--front .dot-field{right:0;top:0;width:360px;height:350px;
    background:radial-gradient(circle at 100% 0%,rgba(74,128,200,.32) 0%,rgba(74,128,200,.12) 45%,rgba(74,128,200,0) 75%)}
  .card--back .dot-field{left:0;top:0;width:340px;height:340px;
    background:radial-gradient(circle at 0% 0%,rgba(74,128,200,.32) 0%,rgba(74,128,200,.12) 45%,rgba(74,128,200,0) 75%)}

  .wordmark{position:absolute;display:flex;align-items:center;gap:10px;font-weight:700;color:var(--ink);line-height:1}
  .wordmark__square{background:var(--brand-blue);flex:none}
  .wordmark__text{display:flex;flex-direction:column}
  .card--front .wordmark{left:23px;top:62px}
  .card--front .wordmark__square{width:44px;height:44px}
  .card--front .wordmark__text{font-size:25px;gap:4px}
  .card--back .wordmark{left:188px;top:156px}
  .card--back .wordmark__square{width:72px;height:72px}
  .card--back .wordmark__text{font-size:40px;gap:6px}

  .holder{position:absolute;left:23px;top:214px}
  .holder__name{font-size:23px;line-height:1;letter-spacing:.2px;color:var(--ink)}
  .holder__name b{font-weight:700}
  .holder__name span{font-weight:400}
  .holder__role{font-size:18px;color:var(--ink-soft);margin-top:9px}

  .divider{position:absolute;left:23px;top:276px;width:650px;height:4px;background:var(--rule-grey);border-radius:2px}
  .divider::before{content:"";position:absolute;left:0;top:0;width:103px;height:4px;background:var(--brand-blue)}

  .contact{position:absolute;top:303px;display:flex;gap:8px;font-size:15.5px;line-height:20px;color:var(--ink-soft)}
  .contact svg{flex:none;width:31px;height:37px}
  .contact--phone{left:23px}
  .contact--web{left:207px}
  .contact--place{left:437px}

  .back-rule{position:absolute;left:23px;top:354px;width:371px;height:4px;background:var(--rule-grey);border-radius:2px}
  .back-site{position:absolute;left:400px;top:338px;display:flex;align-items:center;gap:9px;font-size:22px;color:var(--ink)}
  .back-site svg{width:31px;height:37px}
</style>
</head>
<body>

<section class="card card--front">
  <div class="dot-field" role="img" aria-label="Fan of fine blue dots radiating from the corner"></div>

  <div class="wordmark">
    <div class="wordmark__square"></div>
    <div class="wordmark__text"><span>MERIDIAN</span><span>CHIROPRACTIC</span></div>
  </div>

  <div class="holder">
    <p class="holder__name"><b>DR. DANA</b> <span>HOLLIS</span></p>
    <p class="holder__role">Chiropractic</p>
  </div>

  <div class="divider"></div>

  <div class="contact contact--phone">
    <svg viewBox="0 0 31 37" aria-hidden="true">
      <path d="M3 0h25a3 3 0 0 1 3 3v34l-15.5-6L0 37V3a3 3 0 0 1 3-3z" fill="var(--rule-grey)"/>
      <path d="M7 13c0-3 17-3 17 0v2h-4v-2h-9v2H7z M9 17h13l2 8H7z" fill="#fff"/>
    </svg>
    <p>(555) 014-2280<br>(555) 014-2280</p>
  </div>

  <div class="contact contact--web">
    <svg viewBox="0 0 31 37" aria-hidden="true">
      <path d="M3 0h25a3 3 0 0 1 3 3v34l-15.5-6L0 37V3a3 3 0 0 1 3-3z" fill="var(--rule-grey)"/>
      <circle cx="15.5" cy="16" r="7.5" fill="none" stroke="#fff" stroke-width="1.6"/>
      <path d="M8 16h15M15.5 8.5c-3 4-3 11 0 15M15.5 8.5c3 4 3 11 0 15" fill="none" stroke="#fff" stroke-width="1.3"/>
    </svg>
    <p>dana@meridianchiro.com<br>www.meridianchiro.com</p>
  </div>

  <div class="contact contact--place">
    <svg viewBox="0 0 31 37" aria-hidden="true">
      <path d="M3 0h25a3 3 0 0 1 3 3v34l-15.5-6L0 37V3a3 3 0 0 1 3-3z" fill="var(--brand-blue)"/>
      <path d="M15.5 7a6 6 0 0 1 6 6c0 4.5-6 11-6 11s-6-6.5-6-11a6 6 0 0 1 6-6z" fill="#fff"/>
      <circle cx="15.5" cy="13" r="2.2" fill="var(--brand-blue)"/>
    </svg>
    <p>4120 N Park Ave, Fairview,<br>OH 45010, United State</p>
  </div>
</section>

<section class="card card--back">
  <div class="dot-field" role="img" aria-label="Fan of fine blue dots radiating from the corner"></div>

  <div class="wordmark">
    <div class="wordmark__square"></div>
    <div class="wordmark__text"><span>MERIDIAN</span><span>CHIROPRACTIC</span></div>
  </div>

  <div class="back-rule"></div>
  <div class="back-site">
    <svg viewBox="0 0 31 37" aria-hidden="true">
      <path d="M3 0h25a3 3 0 0 1 3 3v34l-15.5-6L0 37V3a3 3 0 0 1 3-3z" fill="var(--brand-blue)"/>
      <circle cx="15.5" cy="16" r="7.5" fill="none" stroke="#fff" stroke-width="1.6"/>
      <path d="M8 16h15M15.5 8.5c-3 4-3 11 0 15M15.5 8.5c3 4 3 11 0 15" fill="none" stroke="#fff" stroke-width="1.3"/>
    </svg>
    <span>www.meridianchiro.com</span>
  </div>
</section>

</body>
</html>
```